Brightmoor Talent company

We require a website for job recruitment company called "Brightmoor Talent"
Our company is specialising in recruitment of skilled labour from Sri Lanka into Australian market.
We would like to include a job advertising plugin where jobs can be listed and applied for .
COPYWRITING MUST BE INCLUDED !

Industry/Entity Type

Recruitment

Coding

Coded - Design and coding required

Number of Pages Required

5+ page

Colors

Designer to choose colors to be used in the design.

```html
<!DOCTYPE html>
<html lang="en">
<head>
<meta charset="utf-8">
<title>Brightmoor Talent</title>
<link href="https://fonts.googleapis.com/css2?family=Catamaran:wght@300;400;500;600;700&family=Playfair+Display:wght@700&display=swap" rel="stylesheet">
<style>
:root{
  --blue:#0457a7;
  --navy:#1c2433;
  --ink:#222;
  --muted:#b9b9b9;
  --card:#f5f4f2;
  --footer:#5b5b5f;
  --footer-nav:#6a6a6e;
  --footer-base:#4c4c50;
  --white:#fff;
}
*{margin:0;padding:0;box-sizing:border-box}
html,body{width:1200px;height:2798px;overflow:hidden;background:var(--white)}
body{position:relative;font-family:'Catamaran',sans-serif;color:var(--ink)}
.abs{position:absolute}
.serif{font-family:'Playfair Display',serif;font-weight:700}
.btn{position:absolute;display:flex;align-items:center;justify-content:center;background:var(--blue);color:var(--white);border-radius:22px;font-weight:700;font-size:17px}

/* header */
.site-header{position:absolute;left:0;top:0;width:1200px;height:98px;background:var(--white)}
.brand{position:absolute;left:120px;top:30px;font-size:27px;line-height:1;color:#3d4656}
.nav-link{position:absolute;top:42px;font-size:17px;color:#222}
.nav-active-bar{position:absolute;left:500px;width:76px;height:3px;background:var(--blue)}
.header-apply{left:981px;top:31px;width:101px;height:40px;font-weight:400;font-size:16px}

/* hero */
.hero-shape{position:absolute;left:0;top:0}
.hero-frame{position:absolute;left:283px;top:321px;width:632px;height:242px;border:1px solid rgba(40,80,150,.6)}
.hero-kicker{left:0;width:1200px;top:334px;text-align:center;color:var(--white);font-size:30px}
.hero-title{left:0;width:1200px;top:366px;text-align:center;color:var(--white);font-size:50px}
.hero-text{left:360px;width:480px;top:432px;text-align:center;color:#e8e8e8;font-size:16px;line-height:24px;font-weight:300}
.hero-btn{left:526px;top:500px;width:147px;height:39px;font-weight:400;font-size:17px}

/* about */
.section-title{font-size:38px;color:#1e1e1e}
.about-title{left:113px;top:680px}
.body-copy{font-size:15px;line-height:24px;letter-spacing:-0.25px;text-align:justify;color:#222}
.about-text{left:117px;top:740px;width:588px}
.about-btn{left:117px;top:953px;width:148px;height:39px}
.about-photo{left:749px;top:722px;width:349px;height:242px;border-radius:0 60px 0 60px;background:linear-gradient(135deg,#3e4a52 0%,#c97a2a 40%,#e8b23a 55%,#d04a1e 80%,#3a4048 100%)}

/* jobs */
.search-title{left:0;width:1200px;top:1044px;text-align:center}
.search-cat{left:155px;top:1127px;width:172px;height:53px;background:var(--navy);color:var(--white);display:flex;align-items:center;justify-content:center;gap:8px;font-size:19px;font-weight:500}
.search-input{left:327px;top:1127px;width:519px;height:53px;border:1px solid #bdbdbd;background:var(--white);color:var(--muted);font-size:19px;display:flex;align-items:center;padding-left:24px}
.search-btn{left:863px;top:1127px;width:183px;height:53px;background:var(--blue);color:var(--white);font-size:19px;font-weight:500;display:flex;align-items:center;justify-content:center}
.job-card{position:absolute;width:471px;height:122px;background:var(--card);border-radius:3px}
.job-age{position:absolute;right:12px;top:10px;font-size:14px;color:var(--muted)}
.job-title{position:absolute;left:22px;top:26px;font-size:28px;color:#1e1e1e}
.job-meta{position:absolute;left:22px;top:68px;font-size:17px;display:flex;align-items:center;gap:4px}
.job-rating{margin-left:12px;font-size:15px;font-weight:600}
.job-apply{left:277px;top:43px;width:147px;height:37px;font-size:16px}
.view-more{left:526px;top:1521px;width:148px;height:39px}

/* testimonials */
.testimonials{left:0;top:1609px;width:1200px;height:519px;background:var(--blue)}
.testi-title{left:0;width:1200px;top:44px;text-align:center;color:var(--white);font-size:40px}
.testi-card{position:absolute;top:120px;width:306px;height:271px;background:var(--white);border-radius:10px;padding:40px 15px 0}
.testi-card::after{content:"";position:absolute;left:143px;bottom:-10px;border-left:10px solid transparent;border-right:10px solid transparent;border-top:10px solid var(--white)}
.testi-text{font-size:15.5px;line-height:24px;text-align:justify;text-align-last:center;color:#333;font-weight:300}
.testi-name{position:absolute;top:415px;width:306px;text-align:center;color:var(--white);font-size:25px;font-weight:500;line-height:1.1}
.testi-role{position:absolute;top:446px;width:306px;text-align:center;color:var(--white);font-size:17px;font-weight:300}

/* recruiter */
.recruiter-title{left:517px;top:2194px}
.recruiter-text{left:517px;top:2258px;width:557px}
.recruiter-btn{left:517px;top:2421px;width:148px;height:39px}

/* footer */
.footer-brand{left:123px;top:2586px;font-size:30px;line-height:34px;color:var(--white)}
.footer-text{left:350px;top:2570px;width:712px;font-size:16px;line-height:24px;color:#e6e6e6;font-weight:300}
.footer-nav{left:0;top:2700px;width:1200px;height:42px;background:var(--footer-nav)}
.footer-link{position:absolute;top:9px;font-size:17px;color:var(--white)}
.footer-base{left:0;top:2742px;width:1200px;height:56px;background:var(--footer-base)}
.copyright{position:absolute;left:123px;top:19px;font-size:13px;color:var(--white)}
.follow{position:absolute;left:896px;top:16px;font-size:16px;font-weight:600;color:var(--white);display:flex;align-items:center;gap:10px}
.social-dot{width:15px;height:15px;border-radius:50%;background:var(--white)}
</style>
</head>
<body>

<svg class="hero-shape" width="1200" height="620" role="img" aria-label="Photo of a welder in protective gloves working amid smoke">
  <defs>
    <linearGradient id="heroGrad" x1="0" y1="0" x2="1" y2="1">
      <stop offset="0" stop-color="#3a3f4a"/>
      <stop offset=".35" stop-color="#2a2f3c"/>
      <stop offset=".55" stop-color="#4a3a2c"/>
      <stop offset="1" stop-color="#1c2436"/>
    </linearGradient>
  </defs>
  <path d="M0,98 H1200 V570 Q1200,617 1150,614 L600,585 L50,614 Q0,617 0,570 Z" fill="url(#heroGrad)"/>
</svg>

<header class="site-header">
  <div class="brand serif">Brightmoor Talent</div>
  <div class="nav-active-bar" style="top:0"></div>
  <a class="nav-link" style="left:514px">Home</a>
  <a class="nav-link" style="left:600px">Jobs</a>
  <a class="nav-link" style="left:677px">About Us</a>
  <a class="nav-link" style="left:787px">Service</a>
  <a class="nav-link" style="left:883px">Contact</a>
  <a class="btn header-apply">Apply Now</a>
  <div class="nav-active-bar" style="top:95px"></div>
</header>

<section>
  <div class="hero-frame"></div>
  <div class="abs hero-kicker serif">Welcome to</div>
  <h1 class="abs hero-title serif">Brightmoor Talent</h1>
  <p class="abs hero-text">We connect skilled tradespeople from Sri Lanka with trusted employers across Australia, from application to arrival.</p>
  <a class="btn hero-btn">Send A Request</a>
</section>

<section>
  <h2 class="abs section-title serif about-title">About Us</h2>
  <p class="abs body-copy about-text">we are recruitment company with the focus on Sri Lanka/ Australia Market. We are searching for skilled labour / professionals with experience and skillset required and we connect these people with employers in Australia. Basically We advertise for a job in Sri Lankan Newspapers and social media, collecting applications, reviewing the suitable candidates , we shortlist candidates and organise job interviews. After short listing of our potential candidates we are passing the detauils onto Australian companies who have demand for the workers. We assist our candidates and industrial clients with all visa related questions/ matters and cooporating with immigration lawyers to arrange adequate work permits and immigration procedures .</p>
  <a class="btn about-btn">Read More</a>
  <div class="abs about-photo" role="img" aria-label="Photo of industrial workers in hard hats joining hands"></div>
</section>

<section>
  <h2 class="abs section-title serif search-title">Search Jobs In Australia</h2>
  <div class="abs search-cat">Job Category
    <svg width="12" height="8" viewBox="0 0 12 8"><path d="M1 1l5 5 5-5" fill="none" stroke="#fff" stroke-width="1.8"/></svg>
  </div>
  <div class="abs search-input">Job Search</div>
  <a class="abs search-btn">Search Jobs</a>

  <div class="job-card" style="left:118px;top:1222px">
    <span class="job-age">12h</span>
    <h3 class="job-title serif">Job Title</h3>
    <div class="job-meta"><svg width="10" height="14" viewBox="0 0 10 14"><path d="M5 0a5 5 0 0 0-5 5c0 4 5 9 5 9s5-5 5-9a5 5 0 0 0-5-5zm0 7a2 2 0 1 1 0-4 2 2 0 0 1 0 4z" fill="#111"/></svg>Australia | City<span class="job-rating">4.5</span><svg width="13" height="13" viewBox="0 0 24 24"><path d="M12 2l3 7 7 .6-5.3 4.6L18.4 22 12 18 5.6 22l1.7-7.8L2 9.6 9 9z" fill="#f5c543"/></svg></div>
    <a class="btn job-apply">Apply Now</a>
  </div>
  <div class="job-card" style="left:613px;top:1222px">
    <span class="job-age">12h</span>
    <h3 class="job-title serif">Job Title</h3>
    <div class="job-meta"><svg width="10" height="14" viewBox="0 0 10 14"><path d="M5 0a5 5 0 0 0-5 5c0 4 5 9 5 9s5-5 5-9a5 5 0 0 0-5-5zm0 7a2 2 0 1 1 0-4 2 2 0 0 1 0 4z" fill="#111"/></svg>Australia | City<span class="job-rating">4.5</span><svg width="13" height="13" viewBox="0 0 24 24"><path d="M12 2l3 7 7 .6-5.3 4.6L18.4 22 12 18 5.6 22l1.7-7.8L2 9.6 9 9z" fill="#f5c543"/></svg></div>
    <a class="btn job-apply">Apply Now</a>
  </div>
  <div class="job-card" style="left:118px;top:1355px">
    <span class="job-age">12h</span>
    <h3 class="job-title serif">Job Title</h3>
    <div class="job-meta"><svg width="10" height="14" viewBox="0 0 10 14"><path d="M5 0a5 5 0 0 0-5 5c0 4 5 9 5 9s5-5 5-9a5 5 0 0 0-5-5zm0 7a2 2 0 1 1 0-4 2 2 0 0 1 0 4z" fill="#111"/></svg>Australia | City<span class="job-rating">4.5</span><svg width="13" height="13" viewBox="0 0 24 24"><path d="M12 2l3 7 7 .6-5.3 4.6L18.4 22 12 18 5.6 22l1.7-7.8L2 9.6 9 9z" fill="#f5c543"/></svg></div>
    <a class="btn job-apply">Apply Now</a>
  </div>
  <div class="job-card" style="left:613px;top:1355px">
    <span class="job-age">12h</span>
    <h3 class="job-title serif">Job Title</h3>
    <div class="job-meta"><svg width="10" height="14" viewBox="0 0 10 14"><path d="M5 0a5 5 0 0 0-5 5c0 4 5 9 5 9s5-5 5-9a5 5 0 0 0-5-5zm0 7a2 2 0 1 1 0-4 2 2 0 0 1 0 4z" fill="#111"/></svg>Australia | City<span class="job-rating">4.5</span><svg width="13" height="13" viewBox="0 0 24 24"><path d="M12 2l3 7 7 .6-5.3 4.6L18.4 22 12 18 5.6 22l1.7-7.8L2 9.6 9 9z" fill="#f5c543"/></svg></div>
    <a class="btn job-apply">Apply Now</a>
  </div>
  <a class="btn view-more">View More</a>
</section>

<section class="abs testimonials">
  <h2 class="abs testi-title serif">Testimonials</h2>
  <div class="testi-card" style="left:120px"><p class="testi-text">Brightmoor Talent found us three qualified welders within weeks. Every candidate arrived well prepared, with visas and paperwork sorted long before the start date. The team kept us informed at each stage and made a complex process feel simple. We will gladly work with them again.</p></div>
  <div class="testi-name" style="left:120px">John Miller</div>
  <div class="testi-role" style="left:120px">Chief Executive</div>
  <div class="testi-card" style="left:447px"><p class="testi-text">Hiring skilled labour from overseas used to take us months. With Brightmoor Talent the shortlist was ready quickly, interviews ran smoothly and the new electricians settled in fast. Their knowledge of both markets is clear in every step. A reliable partner for our growing business.</p></div>
  <div class="testi-name" style="left:447px">John Miller</div>
  <div class="testi-role" style="left:447px">Chief Executive</div>
  <div class="testi-card" style="left:770px"><p class="testi-text">We needed experienced carpenters for a major project and Brightmoor Talent delivered. They screened every applicant carefully, arranged the interviews and guided the workers through the visa process. The result was a strong, motivated crew. Honest advice and genuine care from start to finish.</p></div>
  <div class="testi-name" style="left:770px">John Miller</div>
  <div class="testi-role" style="left:770px">Chief Executive</div>
</section>

<section>
  <svg class="abs" style="left:70px;top:2192px" width="424" height="272" role="img" aria-label="Photo of two business people shaking hands">
    <defs>
      <linearGradient id="shakeGrad" x1="0" y1="0" x2="1" y2="1">
        <stop offset="0" stop-color="#e9e6e0"/>
        <stop offset=".5" stop-color="#d9a98a"/>
        <stop offset="1" stop-color="#3a3f4c"/>
      </linearGradient>
    </defs>
    <polygon points="62,6 414,6 361,264 8,264" fill="url(#shakeGrad)" stroke="#0457a7" stroke-width="6"/>
  </svg>
  <h2 class="abs section-title serif recruiter-title">Recruiter</h2>
  <p class="abs body-copy recruiter-text">Are you an Australian employer looking for dependable skilled workers? Tell us about the roles you need to fill and we will handle the rest. We advertise across Sri Lanka, screen applicants for experience and qualifications, and present a shortlist of candidates ready to interview. Once you choose your team, we work with immigration lawyers to arrange visas and work permits, so your new staff arrive prepared and on time.</p>
  <a class="btn recruiter-btn">Read More</a>
</section>

<footer>
  <svg class="abs" style="left:0;top:2490px" width="1200" height="308">
    <path d="M0,55 Q0,7 50,10 L600,30 L1150,10 Q1200,7 1200,55 V308 H0 Z" fill="#5b5b5f"/>
  </svg>
  <div class="abs footer-brand serif">Brightmoor<br>Talent</div>
  <p class="abs footer-text">we are recruitment company with the focus on Sri Lanka/ Australia Market .We are searching for skilled labour / proffessionals with experience and skillset required and we connect these people with employers in Australia. Basically We advertise for a job in Sri Lankan Newspapers and social media, collecting applications, reviewing the suitable candidates , we shortlist candidates and organise job interviews.</p>
  <nav class="abs footer-nav">
    <a class="footer-link" style="left:300px">Home</a>
    <a class="footer-link" style="left:430px">Jobs</a>
    <a class="footer-link" style="left:549px">About Us</a>
    <a class="footer-link" style="left:702px">Service</a>
    <a class="footer-link" style="left:840px">Contact</a>
  </nav>
  <div class="abs footer-base">
    <span class="copyright">© copyrights 2022 Brightmoor Talent | All Rights Reserved</span>
    <div class="follow">Follow us :
      <span class="social-dot" aria-label="Social profile"></span>
      <span class="social-dot" aria-label="Video channel"></span>
      <span class="social-dot" aria-label="Social feed"></span>
    </div>
  </div>
</footer>

</body>
</html>
```